Woman owned consulting company needs an elegant and modern business card design

I need a business card design for my new consulting company, Mara Quillon Consulting. I am looking for something that is simple and elegant, but also creative and original. You can use either version of the logo that are attached. I have also included the information that needs to be featured on the business card.

Contact Information for Business Card

Requirements
Must have
• The logo and the font type and a standard business card size. Use shades of gray/silver and or rose gold that are in the logo.
• I didn't realize that my actual logo wasn't attached. Please incorporate in the designs.
Should not have
• Colors that are different from my logo

```html
<!DOCTYPE html>
<html lang="en">
<head>
<meta charset="utf-8">
<title>Mara Quillon Consulting – Business Card</title>
<link rel="stylesheet" href="https://fonts.googleapis.com/css2?family=Cormorant+Garamond:wght@400;500;700&display=swap">
<style>
  :root {
    --backdrop: #3b3b3c;
    --card: #111113;
    --silver: #b9b9bb;
    --silver-dim: #8e8e91;
    --ink-light: #e6e6e6;
  }
  * { margin: 0; padding: 0; box-sizing: border-box; }
  html, body { width: 799px; height: 1200px; overflow: hidden; }
  body {
    background: var(--backdrop);
    font-family: "Cormorant Garamond", Georgia, serif;
    display: flex;
    flex-direction: column;
    align-items: center;
    justify-content: center;
    gap: 110px;
  }
  .card {
    position: relative;
    width: 630px;
    height: 360px;
    background: var(--card);
    box-shadow: 0 14px 30px rgba(0,0,0,0.45);
  }
  .card-front {
    display: flex;
    align-items: center;
    justify-content: center;
  }
  .brand-name {
    color: var(--silver);
    font-weight: 500;
    font-size: 40px;
    letter-spacing: 1px;
    text-align: center;
    line-height: 1.1;
  }
  .card-back .holder {
    position: absolute;
    left: 44px;
    top: 38px;
  }
  .holder-name {
    color: var(--ink-light);
    font-weight: 700;
    font-size: 21px;
    letter-spacing: 1.5px;
    text-transform: uppercase;
  }
  .holder-role {
    color: var(--silver-dim);
    font-size: 13px;
    margin-top: -2px;
  }
  .card-back .brand-name {
    position: absolute;
    right: 44px;
    top: 140px;
    font-size: 34px;
    text-align: right;
  }
  .contact-list {
    position: absolute;
    left: 44px;
    bottom: 46px;
    list-style: none;
  }
  .contact-list li {
    display: flex;
    align-items: center;
    gap: 9px;
    color: var(--ink-light);
    font-size: 15px;
    line-height: 22px;
  }
  .contact-list svg { width: 11px; height: 11px; fill: var(--ink-light); flex: none; }
</style>
</head>
<body>
  <section class="card card-front">
    <p class="brand-name">Mara Quillon Consulting</p>
  </section>

  <section class="card card-back">
    <div class="holder">
      <p class="holder-name">Mara Quillon</p>
      <p class="holder-role">Owner</p>
    </div>
    <p class="brand-name">Mara Quillon<br>Consulting</p>
    <ul class="contact-list">
      <li>
        <svg viewBox="0 0 12 12" aria-hidden="true"><path d="M1 3c0-1 1-2 2-2h6c1 0 2 1 2 2v1H8V3H4v1H1zM2 5h8l1 6H1z"/></svg>
        610-555-0142
      </li>
      <li>
        <svg viewBox="0 0 12 12" aria-hidden="true"><path d="M0 2h12v8H0zM1 3l5 4 5-4v-.2H1z" fill-rule="evenodd"/></svg>
        mara@maraquillonconsulting.com
      </li>
      <li>
        <svg viewBox="0 0 12 12" aria-hidden="true"><circle cx="6" cy="6" r="5.5" fill="none" stroke="#e6e6e6" stroke-width="1"/><ellipse cx="6" cy="6" rx="2.3" ry="5.5" fill="none" stroke="#e6e6e6" stroke-width="0.8"/><path d="M0.5 6h11" stroke="#e6e6e6" stroke-width="0.8"/></svg>
        www.maraquillonconsulting.com
      </li>
    </ul>
  </section>
</body>
</html>
```